VOMRA Pty Ltd Business Card

Looking for a simple yet eye-catching double-sided business card design using my company logo on one side and contact details on the other.

Target Market(s)

Government

Industry/Entity Type

Communication Systems Engineering

Contact Information for Business Card

VOMRA Pty Ltd

Requirements
Nice to have
• Would be great to have a QR code so details can be scanned into contacts

```html
<!DOCTYPE html>
<html lang="en">
<head>
<meta charset="utf-8">
<title>VOMRA Pty Ltd Business Card</title>
<link href="https://fonts.googleapis.com/css2?family=Open+Sans:wght@400;700&display=swap" rel="stylesheet">
<style>
  :root {
    --backdrop: #222222;
    --slate: #37424b;
    --slate-light: #5d6a74;
    --paper: #ffffff;
    --ink: #2f3a42;
    --ink-soft: #1f262b;
  }
  * { margin: 0; padding: 0; box-sizing: border-box; }
  html, body {
    width: 1200px; height: 780px; overflow: hidden;
    background: var(--backdrop);
    font-family: "Open Sans", sans-serif;
  }
  .stage {
    width: 1200px; height: 780px;
    display: flex; align-items: center; justify-content: center; gap: 40px;
  }
  .card {
    position: relative;
    width: 520px; height: 300px;
    border-radius: 18px; overflow: hidden;
    box-shadow: 0 10px 24px rgba(0,0,0,.55);
  }
  .card-shape { position: absolute; inset: 0; }
  .brand {
    position: absolute; display: flex; align-items: center; gap: 14px;
  }
  .brand-dot { border-radius: 50%; }
  .brand-name { font-weight: 700; letter-spacing: 4px; line-height: 1; }

  .card-front .brand { left: 120px; top: 118px; }
  .card-front .brand-dot { width: 44px; height: 44px; background: var(--slate-light); }
  .card-front .brand-name { font-size: 56px; color: var(--slate-light); }

  .card-back .brand { left: 52px; top: 160px; }
  .card-back .brand-dot { width: 30px; height: 30px; background: var(--ink); }
  .card-back .brand-name { font-size: 38px; color: var(--ink); }

  .divider {
    position: absolute; left: 262px; top: 84px;
    width: 1px; height: 150px; background: var(--ink-soft);
  }
  .contact {
    position: absolute; left: 282px; top: 68px;
    color: var(--ink-soft);
  }
  .contact-name { font-size: 19px; font-weight: 700; color: var(--ink); line-height: 1.1; }
  .contact-title { font-size: 11.5px; font-weight: 700; margin-top: 3px; }
  .contact-address { font-size: 11px; line-height: 1.35; margin-top: 12px; }
  .contact-list { list-style: none; margin-top: 12px; font-size: 11.5px; }
  .contact-list li { display: flex; align-items: center; gap: 7px; line-height: 1.55; }
  .contact-list svg { width: 11px; height: 11px; fill: var(--ink); }
</style>
</head>
<body>
<main class="stage">

  <section class="card card-front" aria-label="Card front">
    <svg class="card-shape" viewBox="0 0 520 300" preserveAspectRatio="none">
      <rect width="520" height="300" fill="var(--paper)"/>
      <ellipse cx="270" cy="120" rx="300" ry="205" transform="rotate(-14 270 120)" fill="var(--slate)"/>
    </svg>
    <div class="brand">
      <span class="brand-dot"></span>
      <span class="brand-name">VOMRA</span>
    </div>
  </section>

  <section class="card card-back" aria-label="Card back">
    <svg class="card-shape" viewBox="0 0 520 300" preserveAspectRatio="none">
      <rect width="520" height="300" fill="var(--slate)"/>
      <ellipse cx="255" cy="170" rx="300" ry="200" transform="rotate(-14 255 170)" fill="var(--paper)"/>
    </svg>
    <div class="brand">
      <span class="brand-dot"></span>
      <span class="brand-name">VOMRA</span>
    </div>
    <div class="divider"></div>
    <div class="contact">
      <p class="contact-name">Daniel Whitcombe</p>
      <p class="contact-title">Co-Founder</p>
      <p class="contact-address">14-16 Harlow Lane Marrick<br>Bay NSW 2044 Australia</p>
      <ul class="contact-list">
        <li><svg viewBox="0 0 24 24"><path d="M6.6 10.8a15.1 15.1 0 0 0 6.6 6.6l2.2-2.2a1 1 0 0 1 1-.25 11.4 11.4 0 0 0 3.6.57 1 1 0 0 1 1 1V20a1 1 0 0 1-1 1A17 17 0 0 1 3 4a1 1 0 0 1 1-1h3.5a1 1 0 0 1 1 1c0 1.25.2 2.45.57 3.57a1 1 0 0 1-.25 1z"/></svg>(802) 555-0164</li>
        <li><svg viewBox="0 0 24 24"><path d="M12 2a10 10 0 1 0 0 20 10 10 0 0 0 0-20zm6.9 6h-2.9a15.7 15.7 0 0 0-1.4-3.6A8 8 0 0 1 18.9 8zM12 4c.8 1.2 1.5 2.5 1.9 4h-3.8c.4-1.5 1.1-2.8 1.9-4zM4.3 14a8 8 0 0 1 0-4h3.4a16 16 0 0 0 0 4zm.8 2h2.9c.3 1.3.8 2.5 1.4 3.6A8 8 0 0 1 5.1 16zM8 8H5.1a8 8 0 0 1 4.3-3.6C8.8 5.5 8.3 6.7 8 8zm4 12c-.8-1.2-1.5-2.5-1.9-4h3.8c-.4 1.5-1.1 2.8-1.9 4zm2.3-6H9.7a14.7 14.7 0 0 1 0-4h4.6a14.7 14.7 0 0 1 0 4zm.3 5.6c.6-1.1 1.1-2.3 1.4-3.6h2.9a8 8 0 0 1-4.3 3.6zm1.7-5.6a16 16 0 0 0 0-4h3.4a8 8 0 0 1 0 4z"/></svg>www.vomra.com.au</li>
        <li><svg viewBox="0 0 24 24"><path d="M2 5h20v14H2zm2 2v.5l8 5 8-5V7zm0 2.9V17h16V9.9l-8 5z"/></svg>admin@vomra.com.au</li>
      </ul>
    </div>
  </section>

</main>
</body>
</html>
```